Business Card - Business Consultancy

Newly Established Company, specializing in Business Consultancy, Human Resource Management, Talent Acquisition and Payroll Solutions.

We need a Business card design which portrays "elegance" and a very sleek yet business-like design. We would like a nice blue trimming (which goes well with the logo) to separate the content of the business card at the top. We would also like to see the design using the color silver either as a background or incorporated into it.

The final design should be a Business card which has colors matching the logo; a nice font; the above-mentioned specifics that adheres to the theme of "a stylish and professional business"

FYI: please do not have too fanciful designs.

Industry/Entity Type

Business Consultant

Contact Information for Business Card

Darren Lim
Business Development Director
Arbor Talent Consulting Private Limited
27 Wexley Street, #05-03B
Harbourgate Trade Building
Singapore 059317
Mobile : (+65) 98354417
Email : dlim@arbortalent-advisory.com
Alternative : arbortalentadvisory@mailbox-example.com

Requirements
Must have
• Nice Blue Trimming matching Logo which separates content, see attached
• Design incorporates either a silver background or the use of the color silver
Should not have
• No Fanciful Designs
• No Childish Designs
• No Overly Complicated Designs

```html
<!DOCTYPE html>
<html lang="en">
<head>
<meta charset="utf-8">
<title>Arbor Talent Consulting – Business Card</title>
<link href="https://fonts.googleapis.com/css2?family=Open+Sans:wght@400;600;700&family=Roboto+Condensed:wght@700&display=swap" rel="stylesheet">
<style>
  :root {
    --stage: #000000;
    --card-white: #ffffff;
    --silver-light: #f1f2f4;
    --silver: #c9cdd2;
    --silver-deep: #a9aeb5;
    --brand-blue: #0a7fc1;
    --brand-green: #7cbb2a;
    --ink: #2b2b2b;
    --ink-soft: #3a3a3a;
  }
  * { margin: 0; padding: 0; box-sizing: border-box; }
  html, body {
    width: 1200px; height: 900px; overflow: hidden;
    background: var(--stage);
    font-family: "Open Sans", Arial, sans-serif;
  }
  .stage { position: relative; width: 1200px; height: 900px; }

  .card {
    position: absolute; top: 275px;
    width: 477px; height: 293px; overflow: hidden;
  }
  .card-front {
    left: 116px;
    background: linear-gradient(180deg, var(--card-white) 0%, var(--card-white) 55%, var(--silver-light) 80%, #e2e4e7 100%);
    border-radius: 0 52px 0 52px;
  }
  .card-back {
    left: 622px; background: var(--brand-blue);
    border-radius: 52px 0 52px 0;
  }

  .holder {
    position: absolute; right: 20px; top: 34px; text-align: right;
  }
  .holder-name {
    color: var(--brand-blue); font-weight: 600; font-size: 17px;
    letter-spacing: 0.2px; line-height: 24px; text-transform: uppercase;
  }
  .holder-role {
    color: var(--brand-green); font-size: 13px; line-height: 18px;
  }

  /* blue trim separating the header from the content, with a silver rule beneath */
  .trim {
    position: absolute; left: 0; right: 20px; top: 84px; height: 3px;
    background: var(--brand-blue);
  }
  .trim::after {
    content: ""; position: absolute; left: 0; right: 0; top: 5px; height: 2px;
    background: linear-gradient(90deg, var(--silver-deep), var(--silver-light) 50%, var(--silver-deep));
  }

  .brand {
    position: absolute; display: flex; align-items: center; gap: 12px;
  }
  .brand-dot { border-radius: 50%; flex: none; }
  .brand-name {
    font-family: "Roboto Condensed", "Arial Narrow", sans-serif;
    font-weight: 700; line-height: 1.05;
  }
  .card-front .brand { left: 32px; top: 106px; }
  .card-front .brand-dot { width: 64px; height: 64px; background: var(--brand-blue); }
  .card-front .brand-name { color: var(--ink); font-size: 20px; }
  .card-back .brand { left: 98px; top: 88px; }
  .card-back .brand-dot { width: 96px; height: 96px; background: var(--card-white); }
  .card-back .brand-name { color: var(--card-white); font-size: 28px; }

  .back-rule {
    position: absolute; left: 98px; right: 98px; top: 210px; height: 2px;
    background: linear-gradient(90deg, transparent, var(--silver) 20%, var(--silver-light) 50%, var(--silver) 80%, transparent);
  }

  .address {
    position: absolute; right: 20px; top: 146px; text-align: right;
    font-style: normal;
    color: var(--ink-soft); font-size: 13px; line-height: 15px;
  }
  .contacts {
    position: absolute; right: 20px; top: 216px; list-style: none;
    color: var(--ink-soft); font-size: 13px; line-height: 18px;
  }
  .contacts li {
    display: flex; justify-content: flex-end; align-items: center; gap: 10px;
  }
  .contacts svg { width: 10px; height: 8px; flex: none; fill: var(--brand-blue); }
</style>
</head>
<body>
<main class="stage">
  <section class="card card-front" aria-label="Business card front">
    <div class="holder">
      <p class="holder-name">Darren Lim</p>
      <p class="holder-role">Business Development Director</p>
    </div>

    <div class="trim" aria-hidden="true"></div>

    <div class="brand">
      <span class="brand-dot"></span>
      <span class="brand-name">Arbor Talent<br>Consulting</span>
    </div>

    <address class="address">
      27 Wexley Street, #05-03B<br>
      Harbourgate Trade Building<br>
      Singapore 059317
    </address>

    <ul class="contacts">
      <li>(+65) 98354417
        <svg viewBox="0 0 10 8" aria-hidden="true"><path d="M0 3 C1 0 9 0 10 3 L8 4 L7 2.5 H3 L2 4 Z M2 4.5 H8 V8 H2 Z"/></svg>
      </li>
      <li>Email : dlim@arbortalent-advisory.com
        <svg viewBox="0 0 10 8" aria-hidden="true"><path d="M0 0 H10 V8 H0 Z M1 1 L5 4.5 L9 1 Z" fill-rule="evenodd"/></svg>
      </li>
      <li>Email : arbortalentadvisory@mailbox-example.com
        <svg viewBox="0 0 10 8" aria-hidden="true"><path d="M0 0 H10 V8 H0 Z M1 1 L5 4.5 L9 1 Z" fill-rule="evenodd"/></svg>
      </li>
    </ul>
  </section>

  <section class="card card-back" aria-label="Business card back">
    <div class="brand">
      <span class="brand-dot"></span>
      <span class="brand-name">Arbor Talent<br>Consulting</span>
    </div>
    <div class="back-rule" aria-hidden="true"></div>
  </section>
</main>
</body>
</html>
```